2-Page Flyer for the Information Session about the Quiet Pathfinder Course

This is a flyer to announce/advertise an evening Information Session about the Quiet Pathfinder Course. This Program aims at mindfully rethinking and redesigning work (and life) for people who feel stuck or not entirely satisfied with their work and/or life (please see draft flyer attached for more details). This Program is property of Bright Meadow, a company that uses a combination of Mindfulness, Design, and Entrepreneurship to help people achieve greater happiness (in their work and lives).

Target Market(s)

People who feel stuck or not entirely satisfied with their work and/or life (please see draft flyer attached for more details)

Font styles to use
Serif
Sans Serif

Colors
ffffff
f37122
33a6d7
acd037

Requirements
Must have
• All of what I will say below is suggestive (I’m not a design expert), and I’m open to divert from it, if it makes sense and feels more interesting.
• I thought initially of a 2-page flyer (please see draft flyer attached). The first page could help people grasp the essence of the event quickly (in 1 or 2 minutes), and then, if they are interested/motivated, they would continue reading through page 2, which has more info about the Program in itself.
• Potential Structure
• Page 1
• . About the Information Session on the Quiet Pathfinder Course
• . Visible Date & Time, Contacts, Venue (and other relevant info)
• . About me (the facilitator)
• Page 2
• . About the Quiet Pathfinder Course
• I include a Powerpoint draft of the flyer with the content. The design is rudimentary and precarious from an aesthetics/organization point of view, and this is mainly where I need help (and maybe in other aspects too!).
• On the flyer, I would like to include:
• . A photo of myself (I attach 1 picture).
• . 1 or 2 beautiful-nature photos (cropped or full). One may have to do with looking at the sky, dreaming, and imagining a new work and life (2 photos with sky and clouds attached). The other has to do with walking the transformation journey (the photo with the person walking through the forest path).
• . bright meadow logo or logos (there are two slightly different ones, that can be used for different purposes). For the first page, I would like the bright meadow logo that has "bright meadow" written on the bottom, with the saying "Stillness, Craft and Venture for Bright Meadow" beneath. This is the main logo. For the 2nd page, you can choose the logo that adapts better.
• - Where it says the "the way out is in" it would be great to have a similar font to the one I attach (see file "Font_the_way_out_is_in.png" and Ankecallig-fg.ttf
Nice to have
• In terms of colours, I would not divert much from the logo colours (and of course white and black). I would like the flyer to be quite white. Almost like fairy-tale white: the white horse, the white snow, the white of the stars, the white heaven. White could be the base colour. White means peace, tranquillity, calm contentment, a smile.
• And then use the other colours. The green of the mindfulness. The blue of the sky, the dreams. And the orange of the sun, the energy, the fire, the action. And maybe the black for text.
• Where it says the "the way out is in" it would be great to have a similar font to the one I attach (see file "Font_the_way_out_is_in".
• I would like this flyer to be a piece of art, in every possible way. Simple, beautiful, ease, light, peaceful, calm happy. Just like the Quiet Pathfinder Course and bright meadow Company that I am creating intends to be. The mission of this Program and Company is to be a designer, a painter (a Picasso) of happier and more fulfilling human lives.
• I am very much looking forward to seeing your proposal(s).

```html
<!DOCTYPE html>
<html lang="en">
<head>
<meta charset="utf-8">
<title>Quiet Pathfinder Course – Information Session Flyer</title>
<link rel="stylesheet" href="https://fonts.googleapis.com/css2?family=Open+Sans:ital,wght@0,300;0,400;0,600;0,700;1,400;1,600&family=Oswald:wght@500;600&family=Caveat:wght@600&display=swap">
<style>
:root{
  --orange:#f37122;
  --blue:#33a6d7;
  --green:#acd037;
  --white:#ffffff;
  --ink:#2b2b2b;
  --grey:#9a9a9a;
  --stage:#d9d9d9;
  --sky-top:#cfe3f2;
  --sky-mid:#9ec3df;
  --hill:#5b7a96;
  --night:#2e3a3f;
}
*{box-sizing:border-box;margin:0;padding:0}
html,body{width:1200px;height:808px;overflow:hidden;background:var(--stage);font-family:"Open Sans",sans-serif;color:var(--ink)}
.page{position:absolute;top:71px;width:494px;height:697px;background:var(--white);overflow:hidden;box-shadow:0 4px 14px rgba(0,0,0,.18)}
.front{left:81px}
.back{left:626px}
p{font-size:8.2px;line-height:1.3;text-align:justify}

/* FRONT */
.session-band{position:absolute;left:0;top:0;width:55px;height:697px;background:var(--green);border-radius:0 50px 50px 0/0 36px 36px 0;z-index:3;display:flex;align-items:center;justify-content:center}
.session-band span{writing-mode:vertical-rl;transform:rotate(180deg);color:var(--white);font-size:31px;font-weight:300;letter-spacing:4px;white-space:nowrap}
.hero{position:absolute;left:55px;top:0;width:439px;height:337px;background:linear-gradient(180deg,var(--sky-top) 0%,#e8f0f6 30%,var(--sky-mid) 52%,var(--hill) 70%,#55705a 85%,var(--night) 100%)}
.brand{position:absolute;left:0;right:0;top:16px;text-align:center}
.brand-dot{width:40px;height:40px;border-radius:50%;background:var(--blue);margin:0 auto 6px}
.brand-name{font-size:20px;font-weight:400;color:var(--blue);line-height:1}
.brand-tag{font-size:7.4px;font-style:italic;color:var(--ink);margin-top:6px}
.course-title{position:absolute;left:0;right:0;top:136px;text-align:center;font-family:"Oswald",sans-serif;font-weight:600;line-height:.98;font-size:38px;text-transform:uppercase}
.course-title .l1{color:#333}
.course-title .l2{color:var(--orange)}
.course-title .l3{color:var(--white)}
.when{position:absolute;left:0;right:0;top:265px;height:72px;background:rgba(30,38,40,.55);text-align:center;color:var(--white)}
.when .date{font-size:18.5px;font-weight:300;margin-top:5px}
.when .date b{font-weight:600}
.when .time{font-size:17px;font-weight:300;line-height:1.15}
.when .venue{font-size:10.5px;margin-top:3px}
.when .venue em{font-style:normal;color:var(--green)}
.intro{position:absolute;left:65px;top:346px;width:412px}
.who-head{position:absolute;left:65px;top:373px;width:412px;display:flex;align-items:center;gap:4px;color:var(--green);font-weight:600;font-size:13.5px;line-height:1.1}
.who-head::after{content:"";flex:1;height:1px;background:var(--green);margin-top:6px}
.who{position:absolute;left:65px;top:394px;width:412px}
.facilitator{position:absolute;left:55px;top:440px;width:439px;height:224px;background:linear-gradient(180deg,#efefef,#f8f8f8)}
.portrait{position:absolute;left:18px;top:64px;width:124px;height:124px;border-radius:50%;background:radial-gradient(circle at 50% 40%,#e8c3bd,#c99790 70%,#b88680);border:2px solid var(--white)}
.fac-text{position:absolute;left:152px;top:12px;width:270px}
.fac-label{font-size:7px;font-style:italic;font-weight:600}
.fac-name{font-size:16.5px;font-weight:600;color:var(--orange);line-height:1.1}
.fac-role{font-size:7px;font-style:italic;font-weight:600;margin-bottom:6px}
.fac-text p{font-size:7.6px;line-height:1.3}
.fac-more{font-size:8px;margin-top:8px;display:flex;align-items:center;gap:3px;white-space:nowrap}
.fac-more a{color:var(--blue);font-weight:600;text-decoration:none}
.dot-ico{display:inline-block;width:9px;height:9px;border-radius:50%;background:var(--blue)}
.booking{position:absolute;left:55px;top:664px;width:439px;height:22px;display:flex;font-size:8px;color:var(--white);align-items:center;white-space:nowrap}
.booking-tab{height:100%;width:96px;flex:none;background:#e5e5e5;color:#5b6a1e;font-style:italic;font-weight:600;font-size:8.4px;display:flex;align-items:center;justify-content:center}
.booking-bar{height:100%;flex:1;background:var(--blue);display:flex;align-items:center;gap:9px;padding-left:8px}
.booking-bar span{display:flex;align-items:center;gap:3px}
.ico{width:9px;height:9px;flex:none}

/* BACK */
.sky{position:absolute;left:0;top:0;width:494px;height:110px;background:linear-gradient(180deg,#b6d3e8,#dce9f3 60%,#eef3f7)}
.back h1{position:absolute;left:20px;top:18px;font-size:21px;font-weight:700;color:var(--orange)}
.back .lead{position:absolute;left:20px;top:48px;width:456px;font-size:8.8px;font-style:italic;line-height:1.32;text-align:left}
.sec-tab{position:absolute;height:21px;padding-left:17px;border-radius:0 12px 12px 0;display:flex;align-items:center;color:var(--white);font-weight:700;font-size:13.5px;letter-spacing:.3px}
.tab-program{left:0;top:131px;width:138px;background:var(--orange)}
.tab-why{left:0;top:335px;width:80px;background:var(--blue)}
.tab-how{left:245px;top:335px;width:73px;background:var(--green);padding-left:13px}
.program{position:absolute;left:18px;top:165px;width:214px}
.program p{font-size:8.8px;line-height:1.25;margin-bottom:9px}
.cycle{position:absolute;left:240px;top:120px;width:254px;height:210px}
.why{position:absolute;left:20px;top:365px;width:212px}
.how{position:absolute;left:258px;top:365px;width:220px}
.why p,.how p{font-size:8.8px;line-height:1.25;margin-bottom:7px}
.divider{position:absolute;left:245px;top:356px;width:1px;height:258px;background:var(--green)}
ol{list-style:none}
ol li{display:flex;gap:8px;font-size:8.8px;line-height:1.22;margin-bottom:6px}
ol li i{flex:none;width:10px;height:10px;border-radius:50%;color:var(--white);font-style:normal;font-size:7px;font-weight:700;display:flex;align-items:center;justify-content:center;margin-top:1px}
.why li i{background:var(--blue)}
.how li i{background:var(--green)}
.forest{position:absolute;left:0;top:550px;width:494px;height:114px;background:linear-gradient(90deg,#3a2e1a,#5a4a2a 35%,#8a7b55 50%,#4a3c22 65%,#2f2615)}
.quote{position:absolute;left:150px;top:15px;text-align:center}
.quote .line{font-family:"Caveat",cursive;font-size:33px;color:var(--white);line-height:1}
.quote .by{font-size:7.5px;font-style:italic;color:var(--orange);margin-top:4px}
.back-brand{position:absolute;left:370px;top:42px;display:flex;align-items:center;gap:6px}
.back-brand .brand-dot{width:30px;height:30px;margin:0}
.back-brand span{font-size:14px;color:var(--white);line-height:1}
.contact-bar{position:absolute;left:0;top:664px;width:494px;height:22px;background:var(--blue);color:var(--white);font-size:8px;display:flex;align-items:center;justify-content:center;gap:9px;white-space:nowrap}
.contact-bar span{display:flex;align-items:center;gap:4px}
</style>
</head>
<body>

<section class="page front">
  <div class="session-band"><span>FREE INFORMATION SESSION</span></div>

  <div class="hero" role="img" aria-label="Photo of clouds over a wide mountain landscape">
    <div class="brand">
      <div class="brand-dot"></div>
      <div class="brand-name">bright meadow</div>
      <div class="brand-tag">Stillness, Craft and Venture for Bright Meadow</div>
    </div>
    <h2 class="course-title"><span class="l1">Quiet</span><br><span class="l2">Pathfinder</span><br><span class="l3">Course</span></h2>
    <div class="when">
      <div class="date">Thursday <b>5th September 2019</b></div>
      <div class="time">19:30 to 21:00</div>
      <div class="venue"><em>Venue:</em> Lantern Coworking, C/ Alder 12, Valdora</div>
    </div>
  </div>

  <p class="intro">The purpose of this <b>free Information Session</b> is to give you a real insight into the <b>Quiet Pathfinder Course</b> and how it can help you make the most of your professional and personal life.</p>
  <h3 class="who-head">WHO CAN COME</h3>
  <p class="who">Whether you come on your own, or with friends or family, you'll be warmly welcomed. The session will take place on Thursday the 5th September 2019, from 19:30 to 21:00, at Lantern Coworking. Please see information below to get in contact or to book a seat.</p>

  <div class="facilitator">
    <div class="portrait" role="img" aria-label="Portrait photo of the facilitator"></div>
    <div class="fac-text">
      <div class="fac-label">Facilitator</div>
      <div class="fac-name">DR TOMAS REYNA</div>
      <div class="fac-role">Visiting Research Fellow, Halden University</div>
      <p>Tomas joined the Halden University School of Management as a Lecturer in Entrepreneurship in 2015. He completed his PhD in Entrepreneurship at Norvale Business School in 2014, receiving the prestigious Society of Management's Arden Doctoral Dissertation Award. He began his business career as a Production Engineer for Corvane, and later as a Sales Engineer for Halbrecht. After his MBA, he served as a Strategy Consultant for Lisbri Business School. Originally from Portugal, Tomas enjoys designing and launching new ideas, international communities, mindfulness retreats, and musical improvisation. He nurtures a close connection to Cedar Hollow Mindfulness Centre, where he has practiced and volunteered over 9 months. He has a broad experience of sharing the benefits of mindfulness with others.</p>
      <div class="fac-more">More about the facilitator: <i class="dot-ico"></i> <a>www.profiles.example/in/tomasreyna</a></div>
    </div>
  </div>

  <div class="booking">
    <div class="booking-tab">Information &amp; Booking</div>
    <div class="booking-bar">
      <span><svg class="ico" viewBox="0 0 10 10"><circle cx="5" cy="5" r="5" fill="#fff"/><rect x="2.3" y="3" width="5.4" height="4" fill="none" stroke="#33a6d7" stroke-width=".8"/><path d="M2.3 3 5 5.2 7.7 3" fill="none" stroke="#33a6d7" stroke-width=".8"/></svg>info@brightmeadow.example</span>
      <span><svg class="ico" viewBox="0 0 10 10"><circle cx="5" cy="5" r="5" fill="#fff"/><path d="M3.3 2.6c.5-.3.8 0 1 .5l.2.6c.1.4-.4.6-.2.9l.9 1c.3.2.5-.3.9-.2l.6.2c.5.2.7.6.3 1-1 1-4.2-2-3.7-4z" fill="#33a6d7"/></svg>+34 600 410 275 <i>(video call and messaging)</i></span>
    </div>
  </div>
</section>

<section class="page back">
  <div class="sky" role="img" aria-label="Soft photo of sky and clouds"></div>
  <h1>What is Quiet Pathfinding</h1>
  <p class="lead">Being mindful means being aware and awake. Entrepreneurship is the creation of a new form of organising. Quiet Pathfinding is then the process of creating or redesigning your work and life with awareness, in a way that is reflective of you, of your passions and values, thus conducing to a greater sense of fulfilment and happiness.</p>

  <div class="sec-tab tab-program">THE PROGRAM</div>
  <div class="program">
    <p><b>The Quiet Pathfinder Course</b> is a <b>4-month long transformative journey</b> designed for people who feel stuck or not entirely satisfied with their professional and/or personal life. It will be of benefit for everyone, at any stage.</p>
    <p>The Program entails a five-hour workshop each month, complemented by two-hour weekly peer support meetings. It combines mindfulness techniques, design thinking methodology, and entrepreneurship frameworks.</p>
  </div>

  <svg class="cycle" viewBox="0 0 254 210" font-family="Open Sans, sans-serif">
    <defs>
      <marker id="ah-g" markerWidth="6" markerHeight="6" refX="3" refY="3" orient="auto"><path d="M0 0 6 3 0 6z" fill="#acd037"/></marker>
      <marker id="ah-b" markerWidth="6" markerHeight="6" refX="3" refY="3" orient="auto"><path d="M0 0 6 3 0 6z" fill="#33a6d7"/></marker>
      <marker id="ah-o" markerWidth="6" markerHeight="6" refX="3" refY="3" orient="auto"><path d="M0 0 6 3 0 6z" fill="#f37122"/></marker>
      <marker id="ah-k" markerWidth="6" markerHeight="6" refX="3" refY="3" orient="auto"><path d="M0 0 6 3 0 6z" fill="#9a9a9a"/></marker>
    </defs>
    <path d="M158 35 Q180 42 188 60" fill="none" stroke="#acd037" stroke-width="1.2" marker-end="url(#ah-g)"/>
    <path d="M193 142 Q186 158 170 165" fill="none" stroke="#33a6d7" stroke-width="1.2" marker-end="url(#ah-b)"/>
    <path d="M80 170 Q62 165 55 148" fill="none" stroke="#f37122" stroke-width="1.2" marker-end="url(#ah-o)"/>
    <path d="M55 64 Q62 44 80 37" fill="none" stroke="#9a9a9a" stroke-width="1.2" marker-end="url(#ah-k)"/>

    <g text-anchor="middle" fill="#fff">
      <circle cx="118" cy="41" r="35" fill="#acd037"/>
      <text x="118" y="37" font-size="6.5">Workshop 1</text>
      <text x="118" y="49" font-size="10.5" font-weight="700">INSIGHT</text>
      <text x="118" y="58" font-size="6" font-style="italic">(5 hours)</text>

      <circle cx="195" cy="103" r="35" fill="#33a6d7"/>
      <text x="195" y="99" font-size="6.5">Workshop 2</text>
      <text x="195" y="111" font-size="10.5" font-weight="700">DESIGN</text>
      <text x="195" y="120" font-size="6" font-style="italic">(5 hours)</text>

      <circle cx="119" cy="163" r="35" fill="#f37122"/>
      <text x="119" y="159" font-size="6.5">Workshop 3</text>
      <text x="119" y="171" font-size="10.5" font-weight="700">EXECUTE</text>
      <text x="119" y="180" font-size="6" font-style="italic">(5 hours)</text>

      <circle cx="49" cy="103" r="35" fill="#b5b5b5"/>
      <text x="49" y="99" font-size="6.5">Workshop 4</text>
      <text x="49" y="111" font-size="10.5" font-weight="700">PRESENT</text>
      <text x="49" y="120" font-size="6" font-style="italic">(5 hours)</text>
    </g>

    <g font-size="6.5" font-style="italic">
      <text x="11" y="52" fill="#9a9a9a">WPS meetings</text>
      <text x="220" y="32" fill="#8fb12a" text-anchor="middle">Weekly Peer Support</text>
      <text x="220" y="41" fill="#8fb12a" text-anchor="middle">(WPS) meetings</text>
      <text x="220" y="50" fill="#8fb12a" text-anchor="middle">(2 hours)</text>
      <text x="16" y="158" fill="#f37122">WPS meetings</text>
      <text x="190" y="166" fill="#33a6d7">WPS meetings</text>
    </g>
  </svg>

  <div class="sec-tab tab-why">WHY</div>
  <div class="sec-tab tab-how">HOW</div>
  <div class="divider"></div>

  <div class="why">
    <p>Many people are not satisfied with their work or life, but they don't know what to do about it. This Program offers you a safe place to conduct your inner journey with collective support, helping you to reflect, design and do something about it. It aims at:</p>
    <ol>
      <li><i>1</i><span>Increasing awareness, clarity and confidence</span></li>
      <li><i>2</i><span>Having a deeper <b><em>insight</em></b> on what makes you happier and what you want</span></li>
      <li><i>3</i><span>Developing a clear <b><em>design</em></b> integrating your intended work and life</span></li>
      <li><i>4</i><span>Start <b><em>executing</em></b> this design.</span></li>
    </ol>
  </div>

  <div class="how">
    <p>This Program differs from existing entrepreneurial programs in many ways:</p>
    <ol>
      <li><i>1</i><span>Uses mindfulness and self analysis to look deeply into yourself</span></li>
      <li><i>2</i><span>Design and execution decisions are based on happiness rather than only financials</span></li>
      <li><i>3</i><span>Holistic and inclusive design process, integrating work and life, and building synergies between your different parts.</span></li>
    </ol>
    <p>The Program's format includes lectures, individual work, group sharing, guided activities, experiential exercises, video, audio, handouts and other resources.</p>
  </div>

  <div class="forest" role="img" aria-label="Photo of a person walking along a forest path between tall trees">
    <div class="quote">
      <div class="line">the way out is in</div>
      <div class="by">Zen Master Anselm Ivo</div>
    </div>
    <div class="back-brand"><div class="brand-dot"></div><span>bright<br>meadow</span></div>
  </div>

  <div class="contact-bar">
    <span><svg class="ico" viewBox="0 0 10 10"><circle cx="5" cy="5" r="5" fill="#fff"/><path d="M3.3 2.6c.5-.3.8 0 1 .5l.2.6c.1.4-.4.6-.2.9l.9 1c.3.2.5-.3.9-.2l.6.2c.5.2.7.6.3 1-1 1-4.2-2-3.7-4z" fill="#33a6d7"/></svg>+34 600 410 275 (video call and messaging)</span>
    <span><svg class="ico" viewBox="0 0 10 10"><circle cx="5" cy="5" r="4.3" fill="none" stroke="#fff" stroke-width="1"/><ellipse cx="5" cy="5" rx="1.8" ry="4.3" fill="none" stroke="#fff" stroke-width=".8"/><path d="M.7 5h8.6" stroke="#fff" stroke-width=".8"/></svg>www.brightmeadow.example</span>
    <span><svg class="ico" viewBox="0 0 10 10"><circle cx="5" cy="5" r="5" fill="#fff"/><rect x="2.3" y="3" width="5.4" height="4" fill="none" stroke="#33a6d7" stroke-width=".8"/><path d="M2.3 3 5 5.2 7.7 3" fill="none" stroke="#33a6d7" stroke-width=".8"/></svg>info@brightmeadow.example</span>
  </div>
</section>

</body>
</html>
```